real esate business card with company logo and name

we need a business card design for a real esate company

The company name is Walsh & Brand Pty Ltd, and we have our logo designed and will upload. We want classic or moden feel. Black or white background. looks more textured. Should include folowinginformations
Owen Walsh and Lucy Brand
Sales Agents & Onsite Manager
p: 07 5948 2063
F: 07 5948 2174
M:0431 857 219
3/42 Marlow Crescent, FERNLEA QLD 4213

We want this business card looks professonal. Thank you in advance.

Industry/Entity Type

Real Estate Agent

Contact Information for Business Card

Owen Walsh and Lucy Brand
Onsite Manager & Sales Agents
p: 07 5948 2063
M:0431 857 219

Font styles to use
Serif

Colors
000000
fbfbfb
333333
959595

Requirements
Must have
• company logo and name, black or white back ground

```html
<!DOCTYPE html>
<html lang="en">
<head>
<meta charset="utf-8">
<title>Walsh &amp; Brand Pty Ltd — Business Card</title>
<link rel="stylesheet" href="https://fonts.googleapis.com/css2?family=Open+Sans:wght@400;600;700&display=swap">
<style>
  :root {
    --ink: #000000;
    --paper: #fbfbfb;
    --charcoal: #333333;
    --grey: #959595;
    --backdrop: #e4e2df;
    --photo-light: #eeece8;
    --photo-warm: #ddd2bc;
  }
  * { box-sizing: border-box; margin: 0; padding: 0; }
  html, body {
    width: 1200px; height: 857px; overflow: hidden;
    background: var(--backdrop);
    font-family: "Open Sans", sans-serif;
  }
  .card {
    position: absolute; left: 75px; top: 128px;
    width: 1050px; height: 600px;
    background: var(--paper);
    box-shadow: 0 6px 24px rgba(0,0,0,.18);
    overflow: hidden;
  }
  .card__photo {
    position: absolute; left: 0; top: 0; width: 440px; height: 600px;
    background: linear-gradient(180deg, var(--photo-light) 0%, var(--photo-warm) 100%);
    clip-path: path("M0 0 L330 0 C 470 170 480 400 395 600 L0 600 Z");
  }
  .card__arc { position: absolute; left: 0; top: 0; width: 1050px; height: 600px; }
  .brand {
    position: absolute; left: 620px; top: 70px; width: 340px;
    display: flex; flex-direction: column; align-items: center; gap: 18px;
  }
  .brand__mark { width: 90px; height: 90px; background: var(--grey); }
  .brand__name {
    font-size: 17px; font-weight: 600; letter-spacing: 2px;
    text-transform: uppercase; color: var(--grey); white-space: nowrap;
  }
  .details {
    position: absolute; right: 60px; top: 238px;
    text-align: right; color: var(--ink);
  }
  .details__names { font-size: 40px; font-weight: 400; line-height: 1.15; white-space: nowrap; }
  .details__role { font-size: 29px; color: var(--charcoal); line-height: 1.3; margin-bottom: 22px; white-space: nowrap; }
  .contact { font-size: 29px; font-weight: 700; line-height: 1.3; }
  .contact__row { display: flex; justify-content: flex-end; align-items: center; gap: 10px; white-space: nowrap; }
  .contact__icon {
    width: 24px; height: 24px; flex: none; background: var(--ink);
    display: inline-flex; align-items: center; justify-content: center;
  }
  .contact__icon svg { width: 16px; height: 16px; }
  .contact__spacer { width: 24px; flex: none; }
</style>
</head>
<body>
  <section class="card">
    <div class="card__photo" role="img" aria-label="Photo of a small model house resting on an open hand"></div>
    <svg class="card__arc" viewBox="0 0 1050 600" aria-hidden="true">
      <path d="M330 0 C 470 170 480 400 395 600" fill="none" stroke="var(--ink)" stroke-width="6"/>
    </svg>

    <div class="brand">
      <div class="brand__mark" aria-hidden="true"></div>
      <div class="brand__name">Walsh &amp; Brand Pty Ltd</div>
    </div>

    <div class="details">
      <p class="details__names">Owen Walsh and Lucy Brand</p>
      <p class="details__role">Onsite Manager &amp; Sales Agents</p>
      <div class="contact">
        <div class="contact__row">0431 857 219
          <span class="contact__icon"><svg viewBox="0 0 16 16"><rect x="4" y="1" width="8" height="14" rx="1.5" fill="none" stroke="#fff" stroke-width="1.6"/><circle cx="8" cy="12.5" r="1" fill="#fff"/></svg></span>
        </div>
        <div class="contact__row">07 5948 2063
          <span class="contact__icon"><svg viewBox="0 0 16 16"><path d="M3 2l3 0 1 3-2 1.5c.8 1.8 2.2 3.2 4 4L10.5 8.5l3 1v3c-6 .5-11-4.5-10.5-10.5z" fill="#fff"/></svg></span>
        </div>
        <div class="contact__row">3/42 Marlow Crescent,
          <span class="contact__icon"><svg viewBox="0 0 16 16"><path d="M8 1a4.5 4.5 0 0 0-4.5 4.5C3.5 9 8 15 8 15s4.5-6 4.5-9.5A4.5 4.5 0 0 0 8 1z" fill="#fff"/><circle cx="8" cy="5.5" r="1.6" fill="#000"/></svg></span>
        </div>
        <div class="contact__row">FERNLEA QLD 4213<span class="contact__spacer"></span></div>
      </div>
    </div>
  </section>
</body>
</html>
```